Kestrelford Therapy and Consulting

Build & publish a WordPress website that advertises and markets my private practice - which is delivering, and consulting in, psychological therapies. I also need to be able to edit content (eg text and images) on the end product thereafter. It should have a call to action on the homepage, links to:
• About me
• For referrers (with link to service fees)
• Contact details – phone#, email address, location, operating hours, and service fees
• Other resources

Target Market(s)

People struggling with mental health, relationships, and/or psychological disorders

Industry/Entity Type

Mental health

Coding

Coded - Design and coding required

Number of Pages Required

4 page

Requirements
Must have
• WordPress
Nice to have
• Please make my logo standout on the home page
Should not have
• No testimonials - they're forbidden for psychologists in Australia

```html
<!DOCTYPE html>
<html lang="en">
<head>
<meta charset="utf-8">
<title>Kestrelford Therapy and Consulting</title>
<link href="https://fonts.googleapis.com/css2?family=DM+Serif+Display&family=Poppins:wght@400;500;600&display=swap" rel="stylesheet">
<style>
:root{
  --teal:#1a9fbf;
  --teal-dark:#13839f;
  --teal-soft:#a9e3ef;
  --ink:#2b2b2b;
  --muted:#555;
  --pale:#f2f3f4;
  --footer:#2f2f2f;
  --white:#fff;
}
*{box-sizing:border-box;margin:0;padding:0}
html,body{width:1200px;height:5106px;overflow:hidden}
body{position:relative;font-family:"Poppins",sans-serif;color:var(--ink);background:var(--white)}
.abs{position:absolute}
.serif{font-family:"DM Serif Display",serif;font-weight:400}
.btn{position:absolute;background:var(--teal-soft);color:var(--ink);font-size:14px;border-radius:18px;text-align:center;line-height:32px;height:32px}
.h2{position:absolute;font-family:"DM Serif Display",serif;color:var(--teal);font-size:52px;line-height:1}
.body-text{font-size:14px;line-height:27px;color:var(--ink)}
.photo{position:absolute}
.frame{position:absolute;border:4px solid var(--teal)}

/* header */
.site-header{position:absolute;left:0;top:0;width:1200px;height:85px;background:var(--white);box-shadow:0 2px 8px rgba(0,0,0,.08);z-index:3}
.brand{position:absolute;left:113px;top:20px;display:flex;align-items:center;gap:10px}
.brand-dot{width:42px;height:42px;border-radius:50%;border:3px solid var(--teal)}
.brand-name{font-family:"DM Serif Display",serif;font-size:26px;line-height:1;color:var(--teal-dark)}
.brand-sub{font-size:8px;letter-spacing:2px;color:var(--teal-dark);margin-top:3px}
.nav{position:absolute;left:466px;top:32px;display:flex;gap:34px;font-size:14px}
.nav-cta{position:absolute;left:962px;top:24px;width:127px;height:38px;line-height:38px;border-radius:19px;background:var(--teal-soft);text-align:center;font-size:14px}

/* hero */
.hero-photo{left:0;top:85px;width:1200px;height:540px;background:linear-gradient(100deg,#c9b49a 0%,#8c7b68 35%,#d9d4cf 60%,#6f86a3 85%,#c7c0b8 100%)}
.hero-card{position:absolute;left:113px;top:204px;width:448px;height:278px;background:var(--white);border-radius:14px;padding:24px 30px}
.hero-card .welcome{font-family:"DM Serif Display",serif;color:var(--teal-dark);font-size:24px}
.hero-card .title{font-family:"DM Serif Display",serif;color:var(--teal);font-size:50px;line-height:1.1;margin-top:6px}
.hero-card .sub{font-family:"DM Serif Display",serif;font-size:32px;line-height:1.1;margin-top:2px}
.hero-card p{font-size:16px;line-height:26px;color:var(--muted);text-align:justify;margin-top:14px}

/* services */
.services-bg{left:0;top:1255px;width:1200px;height:609px;background:var(--pale)}
.service-card{position:absolute;top:1422px;width:309px;height:355px;background:var(--white);box-shadow:0 3px 10px rgba(0,0,0,.12);text-align:center}
.service-card .photo{position:relative;height:228px}
.service-card h3{font-weight:500;color:var(--teal);font-size:21px;margin-top:10px}
.service-card p{font-size:13px;line-height:22px;color:var(--muted);margin-top:4px;padding:0 18px}
.service-card a{font-size:13px;color:var(--ink);text-decoration:underline}
.arrow{position:absolute;top:1576px;width:56px;height:56px}

/* interest */
.interest{position:absolute;top:2040px;width:164px;text-align:center}
.interest .ring{width:164px;height:164px;border-radius:50%;border:10px solid var(--teal);display:flex;align-items:center;justify-content:center}
.interest .ring span{width:116px;height:116px;border-radius:50%;background:#eef6f8}
.interest p{color:var(--teal);font-weight:500;font-size:18px;line-height:27px;margin-top:20px}
.dots{position:absolute;top:2315px;left:529px;display:flex;gap:18px}
.dots i{width:22px;height:22px;border-radius:50%;background:#cfcfcf;display:block}
.dots i.on{background:var(--teal)}

/* associations */
.assoc-band{left:0;top:2423px;width:1200px;height:520px;background:linear-gradient(90deg,#179cbd,#1ca8c9)}
.assoc-list{position:absolute;left:113px;top:2588px;width:530px;list-style:none;color:var(--white);font-size:17px;line-height:34px}
.assoc-list li{padding-left:28px;position:relative}
.assoc-list li::before{content:"";position:absolute;left:0;top:12px;width:12px;height:12px;border-radius:50%;background:var(--white)}

/* modalities */
.mod-grid{position:absolute;left:172px;top:3208px;display:grid;grid-template-columns:153px 256px 260px 200px;row-gap:16px;font-size:18px}
.mod-grid div{display:flex;align-items:center;gap:16px}
.mod-grid div::before{content:"";width:20px;height:20px;border-radius:50%;background:#14374a;flex:none}

/* quality */
.quality-bg{left:0;top:3430px;width:1200px;height:492px;background:var(--pale)}

/* tabs */
.tab-box{position:absolute;left:109px;top:4010px;width:980px;height:283px;border:2px solid var(--teal)}
.tab-bar{position:absolute;left:145px;top:4010px;width:912px;height:75px;background:var(--teal);display:flex;align-items:center;padding:0 12px;color:var(--white);font-size:19px;font-weight:500}
.tab-bar span{flex:1;text-align:center}
.tab-bar span.active{background:var(--white);color:var(--teal);border-radius:26px;height:52px;line-height:52px;flex:0 0 198px;margin:0 18px;font-size:22px;font-weight:400}

/* footer */
.site-footer{left:0;top:4769px;width:1200px;height:337px;background:var(--footer);color:var(--white)}
.site-footer h4{font-family:"DM Serif Display",serif;font-size:20px;position:absolute}
.site-footer ul{list-style:none;position:absolute;font-size:14px;line-height:27px}
.fnote{position:absolute;font-size:14px;line-height:22px}
.fsmall{font-size:14px;line-height:20px}
</style>
</head>
<body>

<header class="site-header">
  <div class="brand">
    <span class="brand-dot"></span>
    <div><div class="brand-name">Kestrelford</div><div class="brand-sub">THERAPY AND CONSULTING</div></div>
  </div>
  <nav class="nav"><span>Home</span><span>About Us</span><span>Services</span><span>Areas Of Special Interest</span></nav>
  <div class="nav-cta">Contact Us</div>
</header>

<section>
  <div class="photo hero-photo" role="img" aria-label="Therapist in conversation with a client in a bright office"></div>
  <svg class="abs" style="left:0;top:560px" width="1200" height="140" viewBox="0 0 1200 140">
    <path d="M0 40 C300 25 450 70 600 110 C800 60 1000 45 1200 30 L1200 140 L0 140Z" fill="#fff"/>
    <path d="M0 40 C300 25 450 70 600 110 C800 60 1000 45 1200 30" fill="none" stroke="#8fd4e5" stroke-width="14"/>
    <path d="M0 55 C300 45 450 85 600 125 C800 75 1000 60 1200 45" fill="none" stroke="#1a9fbf" stroke-width="4"/>
  </svg>
  <div class="hero-card">
    <div class="welcome">Welcome To</div>
    <div class="title">Kestrelford</div>
    <div class="sub">Therapy and Consulting</div>
    <p>I'm a clinical psychologist, psychotherapist, EMDR Consultant, and Resource Therapy Practitioner and Trainer.</p>
  </div>
</section>

<section>
  <div class="frame" style="left:160px;top:830px;width:417px;height:340px"></div>
  <div class="photo" style="left:115px;top:787px;width:440px;height:355px;background:linear-gradient(135deg,#3d5a3a,#7f8f6e 60%,#c8b9a5)" role="img" aria-label="Portrait of the psychologist"></div>
  <h2 class="h2" style="left:621px;top:780px">About Me</h2>
  <div class="abs" style="left:621px;top:850px;font-size:21px;font-weight:500">Mr Daniel Hartwell BAppSc(Hons), MPsych(Clin)</div>
  <div class="abs" style="left:621px;top:882px;font-size:16px">Clinical Psychologist, Clinical Supervisor</div>
  <p class="abs body-text" style="left:621px;top:922px;width:470px">I'm a clinical psychologist, psychotherapist, EMDR Consultant, and Resource Therapy Practitioner and Trainer. My main interest in therapy is helping people overcome the inner obstacles that cause them emotional pain and suffering, and that maintain behavioural patterns that are damaging or self-defeating. I also like to train, coach and mentor other therapists in effective therapies.</p>
  <div class="btn" style="left:621px;top:1121px;width:128px">Read More</div>
</section>

<section>
  <div class="photo services-bg"></div>
  <h2 class="h2" style="left:0;width:1200px;text-align:center;top:1335px">Our Services</h2>
  <svg class="arrow" style="left:37px" viewBox="0 0 56 56"><circle cx="28" cy="28" r="26" fill="none" stroke="#333" stroke-width="2"/><path d="M32 16 L20 28 L32 40" fill="none" stroke="#333" stroke-width="2.5"/></svg>
  <svg class="arrow" style="left:1106px" viewBox="0 0 56 56"><circle cx="28" cy="28" r="26" fill="none" stroke="#333" stroke-width="2"/><path d="M24 16 L36 28 L24 40" fill="none" stroke="#333" stroke-width="2.5"/></svg>
  <article class="service-card" style="left:112px">
    <div class="photo" style="background:linear-gradient(135deg,#d9d2c7,#8a7a68)" role="img" aria-label="Psychotherapy session between two people"></div>
    <h3>Psychotherapy</h3><p>Lorem ipsum dolor sit amet, consecte adipiscing elit, sed do</p><a>Learn More</a>
  </article>
  <article class="service-card" style="left:446px">
    <div class="photo" style="background:linear-gradient(135deg,#9aa6b4,#e4e1dc)" role="img" aria-label="Person completing an assessment on a laptop"></div>
    <h3>Assessment</h3><p>Lorem ipsum dolor sit amet, consecte adipiscing elit, sed do</p><a>Learn More</a>
  </article>
  <article class="service-card" style="left:780px">
    <div class="photo" style="background:linear-gradient(135deg,#e9e9e9,#5a6b7e)" role="img" aria-label="Online professional training session on a laptop"></div>
    <h3>Professional Training</h3><p>Lorem ipsum dolor sit amet, consecte adipiscing elit, sed do</p><a>Learn More</a>
  </article>
</section>

<section>
  <h2 class="h2" style="left:0;width:1200px;text-align:center;top:1942px">Area Of Special Interest</h2>
  <div class="interest" style="left:112px"><div class="ring" role="img" aria-label="Addiction icon"><span></span></div><p>Addiction</p></div>
  <div class="interest" style="left:317px"><div class="ring" role="img" aria-label="Anger icon"><span></span></div><p>Anger Related<br>Issues</p></div>
  <div class="interest" style="left:519px"><div class="ring" role="img" aria-label="Panic attack icon"><span></span></div><p>Panic Attacks</p></div>
  <div class="interest" style="left:721px"><div class="ring" role="img" aria-label="Dual diagnosis icon"><span></span></div><p>Dual<br>Diagnosis</p></div>
  <div class="interest" style="left:925px"><div class="ring" role="img" aria-label="Existential issues icon"><span></span></div><p>Existential<br>Issues</p></div>
  <div class="dots"><i></i><i class="on"></i><i></i><i></i></div>
</section>

<section>
  <div class="photo assoc-band"></div>
  <h2 class="h2" style="left:113px;top:2500px;color:var(--white);font-size:48px">Professional Associations</h2>
  <ul class="assoc-list">
    <li>National Psychology Council</li>
    <li>Trauma Therapies Association (Accredited Practitioner &amp; Consultant)</li>
    <li>Parts Therapy Institute (Clinical Resource Therapist &amp; Trainer)</li>
  </ul>
  <div class="btn" style="left:113px;top:2773px;width:128px;background:var(--teal-soft)">Read More</div>
  <div class="frame" style="left:690px;top:2543px;width:358px;height:314px;border-color:var(--white)"></div>
  <div class="photo" style="left:710px;top:2510px;width:377px;height:322px;background:linear-gradient(135deg,#7a8a3c,#d8b86a 55%,#5d6b3a)" role="img" aria-label="Group of friends sitting outdoors talking"></div>
</section>

<section>
  <h2 class="h2" style="left:0;width:1200px;text-align:center;top:3020px">Modalities</h2>
  <p class="abs" style="left:190px;top:3100px;width:820px;text-align:center;font-size:14px;line-height:27px">I believe that using Eye Movement Desensitizing and Reprocessing (EMDR) therapy and Resource Therapy (RT) together addresses almost all mental illness that doesn't involve an organic component. EMDR principally addresses disturbing memories from the past that negatively impact a person in the present.</p>
  <div class="mod-grid">
    <div>EMDR</div><div>Existential</div><div>Integrative</div><div>Mindfulness</div>
    <div>CBT</div><div>Person Centred</div><div>Psychodynamic</div><div>Person Centred</div>
  </div>
  <div class="btn" style="left:536px;top:3310px;width:128px">Read More</div>
</section>

<section>
  <div class="photo quality-bg"></div>
  <div class="frame" style="left:160px;top:3554px;width:415px;height:290px"></div>
  <div class="photo" style="left:113px;top:3516px;width:438px;height:297px;background:linear-gradient(135deg,#c98a4e,#7a5238 50%,#e6c9a2)" role="img" aria-label="Two people embracing in support"></div>
  <h2 class="h2" style="left:617px;top:3510px">Quality Provision</h2>
  <p class="abs body-text" style="left:617px;top:3588px;width:470px">I generally start sessions checking with how clients are feeling and coping between sessions, ascertaining whether or not the client believes we are &quot;on track&quot; according to what was agreed in the treatment plan we co-created. I endeavour to maximise the benefit we can obtain from the number of sessions available to us.</p>
  <div class="btn" style="left:617px;top:3760px;width:128px">Read More</div>
</section>

<section>
  <div class="tab-box"></div>
  <div class="tab-bar"><span>Appointments</span><span>Transport &amp; Parking</span><span class="active">Fees</span><span>Payment Option</span></div>
  <p class="abs" style="left:210px;top:4120px;width:780px;text-align:center;font-size:14px;line-height:27px">My standard fee for a 50 to 60 minute psychological therapy session is $220. For those who are on low or no income my concession fee is $180. Medicare currently rebates 137.05 for a 50+ minute psychological therapy session if a MHCP is in place.</p>
  <div class="btn" style="left:536px;top:4223px;width:128px">Read More</div>
</section>

<section>
  <h2 class="h2" style="left:113px;top:4374px">For Referrers</h2>
  <p class="abs body-text" style="left:113px;top:4452px;width:470px">I generally start sessions checking with how clients are feeling and coping between sessions, ascertaining whether or not the client believes we are &quot;on track&quot; according to what was agreed in the treatment plan we co-created. I endeavour to maximise the benefit we can obtain from the number of sessions available to us.</p>
  <div class="btn" style="left:113px;top:4625px;width:128px">Service Fees</div>
  <div class="frame" style="left:630px;top:4413px;width:415px;height:290px"></div>
  <div class="photo" style="left:656px;top:4382px;width:431px;height:288px;background:linear-gradient(135deg,#d7dde4,#7d8fa3 55%,#eef0f2)" role="img" aria-label="Distressed person being comforted by a clinician"></div>
</section>

<footer class="photo site-footer">
  <div class="abs" style="left:113px;top:50px;display:flex;align-items:center;gap:10px">
    <span style="width:40px;height:40px;border-radius:50%;border:3px solid #fff;display:block"></span>
    <div><div style="font-family:'DM Serif Display',serif;font-size:25px;line-height:1">Kestrelford</div><div style="font-size:8px;letter-spacing:2px;margin-top:3px">THERAPY AND CONSULTING</div></div>
  </div>
  <p class="fnote" style="left:113px;top:112px;width:270px;line-height:26px;text-align:justify">When I first started to practice, I felt ill-prepared for the vast range of maladies of the human condition</p>
  <h4 style="left:429px;top:50px">Quick Links</h4>
  <ul style="left:429px;top:88px"><li>Home</li><li>About Us</li><li>Services</li><li>Area Of Special Interest</li><li>Contact Us</li></ul>
  <h4 style="left:651px;top:50px">Contact Us</h4>
  <svg class="abs" style="left:650px;top:96px" width="12" height="16" viewBox="0 0 12 16"><path d="M6 0a6 6 0 0 0-6 6c0 4.5 6 10 6 10s6-5.5 6-10a6 6 0 0 0-6-6zm0 8.5A2.5 2.5 0 1 1 6 3.5a2.5 2.5 0 0 1 0 5z" fill="#fff"/></svg>
  <p class="abs fsmall" style="left:677px;top:92px;width:200px">Suite 4, Harbour House, 18 Wattle Street, Kestrelford, TAS 7000</p>
  <svg class="abs" style="left:650px;top:168px" width="14" height="14" viewBox="0 0 14 14"><circle cx="7" cy="7" r="7" fill="#fff"/><path d="M7 3v4l3 2" stroke="#2f2f2f" stroke-width="1.6" fill="none"/></svg>
  <p class="abs fsmall" style="left:677px;top:165px">Mon -Fri : 10am to 7.30pm</p>
  <svg class="abs" style="left:905px;top:95px" width="14" height="14" viewBox="0 0 14 14"><path d="M3 0l3 3-2 2c1 2 3 4 5 5l2-2 3 3-2 3C6 14 0 8 0 3z" fill="#fff"/></svg>
  <p class="abs fsmall" style="left:932px;top:92px">0400 555 012</p>
  <svg class="abs" style="left:905px;top:120px" width="15" height="11" viewBox="0 0 15 11"><rect width="15" height="11" rx="1" fill="#fff"/><path d="M0 1l7.5 5L15 1" stroke="#2f2f2f" stroke-width="1.3" fill="none"/></svg>
  <p class="abs fsmall" style="left:932px;top:116px">info@kestrelford.example</p>
  <div class="abs" style="left:113px;top:274px;width:976px;height:1px;background:#666"></div>
  <p class="abs fsmall" style="left:0;width:1200px;text-align:center;top:298px">© 2024 Kestrelford Therapy &amp; Consulting. All Rights Reserved &nbsp;|&nbsp; Sitemap &nbsp;|&nbsp; Privacy Policy</p>
</footer>

</body>
</html>
```